VENTURE CAPITAL GROUP BUSINESS CARD DESIGN

Venture Capital Group based in SF looking for a bold business card design. No trendy colour explosion, 3D effects etc. Just "simple" optical effects. Works on your brain, keeps your eye focused and sticks to your mind.
Target Market(s)
Technology startups
Industry/Entity Type
Venture Capital
Contact Information for Business Card
DESMOND WHITLAKE
MANAGING PARTNER
187 FENWORTH ST SAN FRANCISCO, CA 94187
415.555.0142 O
415.555.0147 F
415.555.0193 C
desmond@veldtmoorcapital.ventures

```html
<!DOCTYPE html>
<html lang="en">
<head>
<meta charset="utf-8">
<title>Veldtmoor Capital Group — Business Card</title>
<link href="https://fonts.googleapis.com/css2?family=Cinzel:wght@400&family=Lora:wght@400&family=Saira+Semi+Condensed:wght@600&display=swap" rel="stylesheet">
<style>
  :root {
    --backdrop: #e6e5e6;
    --card: #fdfdfd;
    --green: #1d7a36;
    --green-dark: #156b2d;
    --ink: #555558;
    --grey-text: #8a8a8d;
    --disc: #ececec;
  }
  * { margin: 0; padding: 0; box-sizing: border-box; }
  html, body { width: 1200px; height: 1200px; overflow: hidden; background: var(--backdrop); }
  .canvas { position: relative; width: 1200px; height: 1200px; }

  .card {
    position: absolute;
    background: var(--card);
    box-shadow: 0 2px 6px rgba(0,0,0,0.08);
  }
  .card--front { left: 238px; top: 118px; width: 713px; height: 420px; }
  .card--back  { left: 230px; top: 644px; width: 712px; height: 417px; }

  .brand-disc {
    position: absolute;
    border-radius: 50%;
    background: radial-gradient(circle at 50% 40%, #fafafa 0%, var(--disc) 70%, #e0e0e0 100%);
  }
  .card--front .brand-disc { left: 281px; top: 88px; width: 152px; height: 152px; }
  .card--back .brand-disc  { left: 50px; top: 82px; width: 200px; height: 200px; }

  .brand-name {
    position: absolute;
    font-family: "Cinzel", serif;
    font-weight: 400;
    color: var(--green);
    text-align: center;
    white-space: nowrap;
  }
  .card--front .brand-name {
    left: 0; right: 0; top: 262px;
    font-size: 44px; line-height: 1.1;
  }
  .card--front .brand-name .brand-sub {
    display: block;
    font-size: 13px;
    letter-spacing: 5px;
    margin-top: 4px;
  }
  .card--back .brand-name {
    left: 50px; width: 200px; top: 166px;
    font-size: 24px; line-height: 1;
  }

  .contact { position: absolute; left: 330px; top: 90px; }
  .contact__name {
    font-family: "Saira Semi Condensed", sans-serif;
    font-weight: 600;
    font-size: 28px;
    color: var(--green-dark);
    line-height: 1.1;
  }
  .contact__title {
    font-family: "Lora", serif;
    font-size: 16px;
    color: var(--grey-text);
    margin-top: 2px;
  }
  .contact__list { list-style: none; margin-top: 40px; }
  .contact__list li {
    display: flex; align-items: center;
    font-family: "Lora", serif;
    font-size: 17px;
    color: var(--ink);
    height: 22.3px;
  }
  .contact__list svg { width: 16px; height: 16px; margin-right: 18px; fill: var(--green-dark); flex: none; }
  .contact__list .accent { color: var(--green); }
  .contact__address {
    font-family: "Lora", serif;
    font-size: 17px;
    color: var(--ink);
    margin-top: 5px;
  }
</style>
</head>
<body>
<div class="canvas">

  <section class="card card--front" aria-label="Card front">
    <div class="brand-disc"></div>
    <h1 class="brand-name">Veldtmoor<span class="brand-sub">CAPITAL GROUP</span></h1>
  </section>

  <section class="card card--back" aria-label="Card back">
    <div class="brand-disc"></div>
    <div class="brand-name">Veldtmoor</div>

    <div class="contact">
      <h2 class="contact__name">Desmond Whitlake</h2>
      <p class="contact__title">Managing Partner</p>
      <ul class="contact__list">
        <li><svg viewBox="0 0 16 16" aria-hidden="true"><path d="M1 6c0-2 3-3 7-3s7 1 7 3v1h-3V5.5H4V7H1z"/><path d="M3 8h10l1 6H2z"/></svg>415.555.0142</li>
        <li><svg viewBox="0 0 16 16" aria-hidden="true"><rect x="4" y="1" width="8" height="4"/><rect x="1" y="6" width="14" height="6" rx="1"/><rect x="4" y="10" width="8" height="5"/></svg>415.555.0147</li>
        <li><svg viewBox="0 0 16 16" aria-hidden="true"><path d="M4 1h8v14H4z M5.5 3v9h5V3z"/></svg>415.555.0193</li>
        <li><svg viewBox="0 0 16 16" aria-hidden="true"><path d="M1 3h14v10H1z M2.5 4.5 8 9l5.5-4.5z" fill-rule="evenodd"/></svg>desmond@veldtmoorcapital.ventures</li>
        <li><svg viewBox="0 0 16 16" aria-hidden="true"><circle cx="8" cy="8" r="7"/><path d="M1 8h14M8 1c-3 3-3 11 0 14M8 1c3 3 3 11 0 14" stroke="#fdfdfd" stroke-width="1" fill="none"/></svg>www.<span class="accent">veldtmoorcapital</span>.ventures</li>
      </ul>
      <p class="contact__address">187 Fenworth St San Francisco, CA 94187</p>
    </div>
  </section>

</div>
</body>
</html>
```